Business card design for Automotive workshop

We need a business card for a new automotive repair and tyre shop called Keelstone Prime Automotive located in New Zealand. We are a clean, modern and fresh workshop and company.

Front needs to feature logo,
my name:
Marlo Fenwicke (director)

Address:
48 Tarn Lane
Whitianga 3510

Phone: 07 594 2713
Mobile: 027 451 9362
Email: office@keelstoneautomotive.example.nz
Website: keelstoneautomotive.example.nz

Back needs to feature an area to write down appointment details, date and time.

Also feature a list of jobs and work we do such as,
Vehicle Servicing
All Mechanical Repairs
Warrant of Fitness
Tyres & Wheel Alignments
Automotive Diagnostics
Automotive Parts & Supplies

```html
<!DOCTYPE html>
<html lang="en">
<head>
<meta charset="utf-8">
<title>Keelstone Prime Automotive – Business Card</title>
<link href="https://fonts.googleapis.com/css2?family=Arimo:wght@400;700&family=Open+Sans:wght@400;600;700&display=swap" rel="stylesheet">
<style>
  :root {
    --red: #e31e24;
    --ink: #2a2a2a;
    --grey-line: #c9c9c9;
    --paper: #ffffff;
    --backdrop: #3b3b3b;
  }
  * { box-sizing: border-box; margin: 0; padding: 0; }
  html, body { width: 1200px; height: 1015px; overflow: hidden; }
  body { background: var(--backdrop); position: relative; font-family: "Arimo", Arial, sans-serif; }

  .card {
    position: absolute; left: 220px; width: 760px; height: 434px;
    background: var(--paper); overflow: hidden;
    box-shadow: 0 10px 24px rgba(0,0,0,.45);
  }
  .card--back { top: 52px; }
  .card--front { top: 529px; }

  /* Back */
  .appointment { position: absolute; left: 150px; top: 58px; width: 440px; }
  .appointment__title {
    color: var(--red); font-weight: 700; font-size: 27px; letter-spacing: .5px;
    text-align: center; margin-bottom: 30px;
  }
  .appointment__row { display: flex; align-items: flex-end; height: 46px; color: var(--ink); font-size: 21px; }
  .appointment__label { width: 82px; }
  .appointment__line { flex: 1; border-bottom: 1px solid var(--grey-line); margin-bottom: 5px; }

  .services {
    position: absolute; left: 0; right: 0; bottom: 0; height: 190px;
    background: var(--red); display: flex; justify-content: space-between;
    padding: 42px 70px 0 90px;
  }
  .services__list { list-style: none; color: #fff; font-size: 21px; line-height: 31px; }
  .services__list li::before {
    content: ""; display: inline-block; width: 9px; height: 9px; border-radius: 50%;
    background: #fff; margin-right: 12px; vertical-align: middle; position: relative; top: -2px;
  }

  /* Front */
  .brand {
    position: absolute; left: 48px; top: 180px; width: 250px;
    color: var(--red); font-weight: 700; font-size: 28px; line-height: 34px; letter-spacing: .5px;
    text-transform: uppercase;
  }
  .divider { position: absolute; left: 330px; top: 80px; width: 1px; height: 240px; background: var(--grey-line); }
  .contact { position: absolute; left: 355px; top: 80px; right: 30px; font-family: "Open Sans", Arial, sans-serif; color: var(--ink); white-space: nowrap; }
  .contact__name { color: var(--red); font-weight: 700; font-size: 24px; text-transform: uppercase; letter-spacing: .3px; }
  .contact__role { font-size: 16px; margin-bottom: 10px; }
  .contact__address { font-size: 17px; line-height: 24px; margin-bottom: 14px; }
  .contact__list { list-style: none; font-size: 16px; line-height: 26px; }
  .contact__list li { display: flex; align-items: center; }
  .contact__list svg { width: 14px; height: 14px; margin-right: 10px; flex: none; }
  .front__strip { position: absolute; left: 0; right: 0; bottom: 0; height: 14px; background: var(--red); }
</style>
</head>
<body>

<section class="card card--back" aria-label="Card back">
  <div class="appointment">
    <h2 class="appointment__title">NEXT APPOINTMENT</h2>
    <div class="appointment__row"><span class="appointment__label">DATE</span><span class="appointment__line"></span></div>
    <div class="appointment__row"><span class="appointment__label">TIME</span><span class="appointment__line"></span></div>
  </div>
  <div class="services">
    <ul class="services__list">
      <li>Vehicle Servicing</li>
      <li>All Mechanical Repairs</li>
      <li>Warrant of Fitness</li>
    </ul>
    <ul class="services__list">
      <li>Tyres &amp; Wheel Alignments</li>
      <li>Automotive Diagnostics</li>
      <li>Automotive Parts &amp; Supplies</li>
    </ul>
  </div>
</section>

<section class="card card--front" aria-label="Card front">
  <div class="brand">Keelstone Prime Automotive</div>
  <div class="divider"></div>
  <div class="contact">
    <div class="contact__name">Marlo Fenwicke</div>
    <div class="contact__role">Director</div>
    <div class="contact__address">48 Tarn Lane<br>Whitianga 3510</div>
    <ul class="contact__list">
      <li><svg viewBox="0 0 16 16" aria-hidden="true"><path fill="#e31e24" d="M3 1h3l1.5 4-2 1.3a9 9 0 0 0 4.2 4.2L11 8.5l4 1.5v3a2 2 0 0 1-2 2A12 12 0 0 1 1 3a2 2 0 0 1 2-2z"/></svg>07 594 2713</li>
      <li><svg viewBox="0 0 16 16" aria-hidden="true"><rect x="3.5" y="1" width="9" height="14" rx="1.5" fill="none" stroke="#e31e24" stroke-width="1.8"/><circle cx="8" cy="12.5" r="1" fill="#e31e24"/></svg>027 451 9362</li>
      <li><svg viewBox="0 0 16 16" aria-hidden="true"><rect x="1" y="3" width="14" height="10" fill="#e31e24"/><path d="M1 3l7 5.5L15 3" fill="none" stroke="#fff" stroke-width="1.3"/></svg>office@keelstoneautomotive.example.nz</li>
      <li><svg viewBox="0 0 16 16" aria-hidden="true"><circle cx="8" cy="8" r="7" fill="#e31e24"/><path d="M1 8h14M8 1c-3 3.5-3 10.5 0 14M8 1c3 3.5 3 10.5 0 14" fill="none" stroke="#fff" stroke-width="1"/></svg>keelstoneautomotive.example.nz</li>
    </ul>
  </div>
  <div class="front__strip"></div>
</section>

</body>
</html>
```